PowerPoint Listing Presentation for Real Estate Agency

We need a PowerPoint presentation for a new real estate brokerage team.

[[[[[[submit 1-3 sample slides for review - i will provide feedback and you can make changes if you want to - we will not be deciding on a design prior to the deadline]]]]]

******ATTN: DESIGNERS, if your skills are webdesign then just look at this like a portable website or a brochure. it should be easy enough******

NOTE: we have all the data to put into the slides. You just need to come up with the design and layout. we have a sample design that we like and have provided.

This focus will be for the home listing side of the business (a presentation for home sellers to convince them to use our services). The data and slides will present our team and the benefits, in the best light, to use our services over that of other real estate agent applying for the job. This presentation will proved facts and benefits and describe our special and unique offerings that will show a home seller why we can sell their home for more money in less time and with the least amount of hassle. The main color scheme is Dark Blue and White (we want some additional colors included - based on your creativity. otherwise the presentation will too monotone). We would like to see the use of Statistical Graphs (3-D) - data provided. We have photos of our team and a new logo (the logo could have some minor adjustment to clean it up if necessary) - also uploaded. We have about 80-90% of the information that will be put into the slides and will need to work closely to get the design and data integrated into the presentation (should be easier then it sounds). We should be able to add slides and data 'at will' over time via our master slides built into the presentation. We have a pretty good sample presentation that we like and can be used as a guideline (this is from our affiliated business network and we have full rights to all the information), it is uploaded but doesn't contain all the slide because of size limitations.

NOTE: An additional buyers presentation will be needed after we get the sellers presentation completed, which means additional work.

This should be enough to get you started and we are available if you have any questions to help you with the project. there will be around 60-70 total slides. once concept is completed it will be easy to create the slides.

Target Market(s)

home sellers. people who are moving to a new and better home or relocation for job reasons. typically more established in life

Industry/Entity Type

Real Estate

Requirements
Must have
• all the slides must be congruent. in other words, the exact same layout feel should used across the board. we are working on building our trade dress/image. Also, it must have a soft and inviting overall feel, yet show strength of ability.
Nice to have
• nice to have use of real people images when necessary. 3D graphs would be nice. clean modern look and feel, yet sophisticated and professional.
Should not have
• should not have a lot of time consuming transitions. do not include 3D stick figures or distracting moving gifs

```html
<!DOCTYPE html>
<html lang="en">
<head>
<meta charset="utf-8">
<title>Harwell &amp; Stone – Listing Presentation Slides</title>
<link rel="stylesheet" href="https://fonts.googleapis.com/css2?family=Open+Sans:wght@400;600;700&display=swap">
<style>
  :root {
    --navy: #15175a;
    --heading-blue: #1c3f9a;
    --bullet-blue: #2a4fb5;
    --text-grey: #555a60;
    --title-grey: #2f3338;
    --sub-grey: #5d6268;
    --frame: #1b1b1d;
    --page-bg: #0f0f10;
    --white: #ffffff;
    --light-1: #f4f5f7;
    --light-2: #dfe2e8;
  }
  * { box-sizing: border-box; margin: 0; padding: 0; }
  html, body {
    width: 1200px; height: 936px; overflow: hidden;
    background: var(--white);
    font-family: "Open Sans", Arial, sans-serif;
  }
  .board {
    position: absolute; left: 24px; top: 24px; width: 1153px; height: 888px;
    background: var(--frame);
  }
  .slide {
    position: absolute; width: 562px; height: 420px; overflow: hidden;
    background: var(--white);
  }
  .slide--s1 { left: 8px; top: 8px; }
  .slide--s2 { left: 576px; top: 8px; }
  .slide--s3 { left: 8px; top: 442px; }
  .slide--s4 { left: 576px; top: 442px; }

  .bg-cover {
    position: absolute; inset: 0;
    background:
      radial-gradient(ellipse at 70% 10%, #ffffff 0%, rgba(255,255,255,0) 55%),
      linear-gradient(180deg, #f7f8fa 0%, #eceef2 55%, var(--light-2) 100%);
  }
  .bg-content {
    position: absolute; inset: 0;
    background:
      radial-gradient(ellipse 70% 40% at 80% 20%, rgba(225,228,234,.9) 0%, rgba(255,255,255,0) 70%),
      linear-gradient(160deg, #ffffff 0%, var(--light-1) 60%, #ffffff 100%);
  }

  .brand-box {
    position: absolute; background: var(--white);
    border: 1px solid var(--navy);
    display: flex; align-items: center; justify-content: center; gap: 12px;
  }
  .brand-box__mark { width: 22px; height: 22px; background: var(--navy); }
  .brand-box__name {
    color: var(--navy); font-weight: 700; font-size: 21px; letter-spacing: .3px;
  }
  .brand-tag {
    position: absolute; background: var(--white); border: 2px solid var(--navy);
    display: flex; align-items: center; justify-content: center;
    color: var(--navy); font-weight: 700; font-size: 11px;
  }

  .cover-title { position: absolute; left: 36px; font-size: 17px; font-weight: 600; color: var(--title-grey); }
  .cover-presenter { position: absolute; left: 36px; font-size: 14.5px; font-weight: 700; color: var(--sub-grey); }

  .page-no { position: absolute; left: 16px; font-size: 11px; font-weight: 700; color: #111; }
  .copyright { position: absolute; font-size: 11px; color: #c9cdf0; }

  .top-band { position: absolute; left: 0; top: 0; width: 100%; height: 19px; background: var(--navy); }
  .footer-band { position: absolute; left: 0; bottom: 0; }

  .slide-title { position: absolute; left: 27px; font-size: 21px; font-weight: 400; color: var(--navy); }
  .slide--s4 .slide-title { color: var(--heading-blue); font-weight: 600; }

  .body-copy { position: absolute; font-size: 10.5px; line-height: 16.5px; color: var(--text-grey); }
  .body-copy--justify { text-align: justify; }

  .bullets { position: absolute; list-style: none; }
  .bullets li {
    position: relative; padding-left: 21px; font-size: 13.5px; color: var(--text-grey);
  }
  .bullets li::before {
    content: "»"; position: absolute; left: 0; top: -1px; color: var(--bullet-blue); font-size: 15px;
  }

  .section-heading { position: absolute; font-size: 14.5px; font-weight: 700; color: var(--heading-blue); }
  .column-divider {
    position: absolute; left: 283px; top: 100px; width: 1px; height: 250px;
    background: linear-gradient(180deg, rgba(200,204,212,0), #c8ccd4 30%, #c8ccd4 70%, rgba(200,204,212,0));
  }

  .photo-slot {
    position: absolute; border: 3px solid var(--white); border-radius: 3px;
    box-shadow: 0 1px 4px rgba(0,0,0,.35);
    background: linear-gradient(180deg, #9cc3e6 0%, #c9dfee 45%, #9ab76a 75%, #c89a7a 100%);
  }
  .skyline-slot {
    position: absolute;
    background: linear-gradient(180deg, rgba(190,192,196,.55) 0%, rgba(160,162,166,.75) 100%);
  }
</style>
</head>
<body>
<main class="board">

  <!-- Cover slide, light -->
  <section class="slide slide--s1">
    <div class="bg-cover"></div>
    <div class="brand-box" style="left:33px; top:165px; width:268px; height:75px;">
      <span class="brand-box__mark"></span>
      <span class="brand-box__name">HARWELL &amp; STONE</span>
    </div>
    <p class="cover-title" style="top:263px;">Insert Title Here</p>
    <p class="cover-presenter" style="top:292px;">Insert Presenter Name Here</p>
    <p class="page-no" style="top:392px;">Page : 01</p>
  </section>

  <!-- Content slide, photo + bullets -->
  <section class="slide slide--s2">
    <div class="bg-content"></div>
    <div class="top-band"></div>
    <h1 class="slide-title" style="top:50px;">Project Title Here</h1>
    <p class="body-copy" style="left:25px; top:89px; width:480px;">
      Lorem ipsum dolor sit ipsum Lorem ipsum dolor sit ipsum Lorem ipsum dolor sit ipsum Lorem
      ipsum dolor sit ipsum Lorem ipsum dolor sit ipsum Lorem ipsum Lorem ipsum dolor sit ipsum
      Lorem ipsum dolor sit ipsum Lorem ipsum dolor sit ipsum Lorem ipsum dolor sit ipsum Lorem
      ipsum dolor sit ipsum Lorem ipsum
    </p>
    <ul class="bullets" style="left:34px; top:175px; line-height:29px;">
      <li>Lorem ipsum dolor sit ipsum</li>
      <li>Lorem ipsum dolor sit ipsum</li>
      <li>Lorem ipsum dolor sit ipsum</li>
      <li>Lorem ipsum dolor sit ipsum</li>
      <li>Lorem ipsum dolor sit ipsum</li>
    </ul>
    <div class="photo-slot" role="img" aria-label="Photo of hands holding a small young tree" style="left:368px; top:193px; width:162px; height:104px;"></div>
    <svg class="footer-band" width="562" height="40" viewBox="0 0 562 40" aria-hidden="true">
      <path d="M67 40 C78 22 84 2 104 1 H562 V40 Z" fill="var(--navy)"/>
    </svg>
    <p class="page-no" style="top:396px;">Page : 02</p>
    <p class="copyright" style="left:125px; top:398px;">Copyright text here</p>
    <div class="brand-tag" style="left:489px; top:367px; width:47px; height:49px;">H&amp;S</div>
  </section>

  <!-- Cover slide, skyline -->
  <section class="slide slide--s3">
    <div class="bg-cover"></div>
    <div class="skyline-slot" role="img" aria-label="Illustration of grey city buildings" style="left:298px; top:133px; width:264px; height:254px;"></div>
    <div class="brand-box" style="left:31px; top:137px; width:269px; height:76px;">
      <span class="brand-box__mark"></span>
      <span class="brand-box__name">HARWELL &amp; STONE</span>
    </div>
    <p class="cover-title" style="top:239px; left:33px;">Insert Title Here</p>
    <p class="cover-presenter" style="top:268px; left:33px;">Insert Presenter Name Here</p>
    <div style="position:absolute; left:78px; top:386px; width:484px; height:34px; background:var(--navy);"></div>
    <p class="page-no" style="top:397px; left:15px;">Page : 01</p>
  </section>

  <!-- Content slide, three columns -->
  <section class="slide slide--s4">
    <div class="bg-content"></div>
    <div class="top-band"></div>
    <div class="brand-tag" style="left:502px; top:0; width:52px; height:50px;">H&amp;S</div>
    <h1 class="slide-title" style="top:47px;">Project Title Here</h1>

    <h2 class="section-heading" style="left:27px; top:97px;">Heading 1</h2>
    <p class="body-copy body-copy--justify" style="left:28px; top:121px; width:238px;">
      Lorem ipsum dolor sit ipsum Lorem ipsum dolor sit ipsum Lorem ipsum dolor sit ipsum
      Lorem ipsum dolor sit ipsum Lorem ipsum dolor sit ipsum Lorem ipsum dolor sit ipsum
      Lorem ipsum dolor sit ipsum Lorem ipsum dolor sit ipsum Lorem ipsum
    </p>
    <h2 class="section-heading" style="left:27px; top:232px;">Heading 2</h2>
    <p class="body-copy body-copy--justify" style="left:28px; top:256px; width:238px;">
      Lorem ipsum dolor sit ipsum Lorem ipsum dolor sit ipsum Lorem ipsum dolor sit ipsum
      Lorem ipsum dolor sit ipsum Lorem ipsum dolor sit ipsum Lorem ipsum dolor sit ipsum
      Lorem ipsum dolor sit
    </p>

    <div class="column-divider"></div>

    <h2 class="section-heading" style="left:302px; top:98px;">Heading 3</h2>
    <ul class="bullets" style="left:302px; top:124px; line-height:28.8px;">
      <li>Lorem ipsum dolor sit ipsum</li>
      <li>Lorem ipsum dolor sit ipsum</li>
      <li>Lorem ipsum dolor sit ipsum</li>
      <li>Lorem ipsum dolor sit ipsum</li>
      <li>Lorem ipsum dolor sit ipsum</li>
      <li>Lorem ipsum dolor sit ipsum</li>
      <li>Lorem ipsum dolor sit ipsum</li>
      <li>Lorem ipsum dolor sit ipsum</li>
    </ul>

    <svg class="footer-band" width="562" height="44" viewBox="0 0 562 44" aria-hidden="true">
      <path d="M67 44 C78 24 84 1 106 0 H562 V44 Z" fill="var(--navy)"/>
    </svg>
    <p class="page-no" style="top:393px;">Page : 02</p>
    <p class="copyright" style="left:126px; top:396px;">Copyright text here</p>
  </section>

</main>
</body>
</html>
```